Super Greens Label for Supplement Bottle

We want to design a front label for a health supplement bottle. The product is called Meadow Crunch Chews™. This will be a new product so there is no current website for the product. The focus is on supergreens that taste great and deliver support for energy, digestion, and immune defense.
We want it to be modern, vibrant and appealing.
Bottle size: standard size supplement CLEAR bottle size, with white child resistant cap and the label panel dimensions are 3” x 7”. The label should be primarily white and green, with a touch of red; (see color palettes)/it can also ONLY be white and green. See samples attached.
We are only focused on the front of the bottle design, not on the back, but leave space for the supplement panel and other text on the back.
So the text for the front of the bottle is:
RT Halvorsen's
Meadow Crunch Chews™
Super Greens Blend for:
Energy, Digestion, and Immune Support*
60 Gummies | Dietary Supplement
Raspberry Flavor Gummies
Off to side of the label:
Non-GMO
Vegan Friendly
Plant-Based
Gelatin Free
Colors
Designer to choose colors to be used in the design.
Look and feel
Each slider illustrates characteristics of the customer's brand and the style your logo design should communicate.

```html
<!DOCTYPE html>
<html lang="en">
<head>
<meta charset="utf-8">
<title>Meadow Crunch Chews – Front Label</title>
<link rel="stylesheet" href="https://fonts.googleapis.com/css2?family=Roboto:wght@300;700;900&family=Roboto+Condensed:wght@500&display=swap">
<style>
  :root {
    --bg: #ffffff;
    --green-bright: #2ba32b;
    --green-band: #1f8f26;
    --green-deep: #1d4f22;
    --green-mid: #2e6b33;
    --green-soft: #4e8a55;
    --rule: #7bcf6d;
    --text: #f2f5f1;
    --berry: #d9415a;
  }
  * { box-sizing: border-box; margin: 0; padding: 0; }
  html, body { width: 1067px; height: 1200px; overflow: hidden; background: var(--bg); }
  body { position: relative; font-family: "Roboto", Arial, sans-serif; color: var(--text); }

  .label {
    position: absolute; left: 90px; top: 200px; width: 887px; height: 800px;
    background: var(--green-deep); overflow: hidden;
  }
  .label__top-band { position: absolute; left: 0; top: 0; width: 100%; height: 46px; background: linear-gradient(180deg, #3fbf45, var(--green-band)); }
  .label__panel {
    position: absolute; left: 0; top: 46px; width: 100%; height: 660px;
    background: linear-gradient(90deg, var(--green-soft) 0%, var(--green-mid) 28%, var(--green-deep) 55%, var(--green-deep) 100%);
  }
  .label__decor {
    position: absolute; left: 30px; top: 90px; width: 300px; height: 520px;
    border-radius: 45% 45% 48% 48%;
    background: radial-gradient(ellipse at center, rgba(255,255,255,0.10), rgba(255,255,255,0));
  }
  .label__bottom-band {
    position: absolute; left: 0; bottom: 0; width: 100%; height: 94px;
    background: linear-gradient(180deg, var(--green-band), var(--green-bright));
    display: flex; align-items: center; justify-content: center;
    font-weight: 700; font-size: 44px; letter-spacing: -0.5px;
  }

  .front { position: absolute; left: 70px; top: 92px; width: 640px; text-align: center; white-space: nowrap; }
  .front__brand { font-weight: 700; font-size: 24px; line-height: 30px; letter-spacing: 3px; opacity: .85; margin-bottom: 4px; }
  .front__title { font-weight: 900; font-size: 70px; line-height: 76px; letter-spacing: -1px; }
  .front__title-sub { font-weight: 300; font-size: 78px; line-height: 82px; }
  .front__blend { font-weight: 700; font-size: 40px; line-height: 48px; margin-top: 18px; letter-spacing: -0.5px; }
  .front__rule { height: 3px; background: var(--rule); margin: 10px 0 18px; }
  .front__benefits { font-weight: 700; font-size: 44px; line-height: 54px; letter-spacing: -0.5px; }
  .front__benefits small { display: block; font-size: 38px; line-height: 46px; }
  .front__count { display: flex; align-items: center; justify-content: center; gap: 18px; margin-top: 14px; font-weight: 900; font-size: 70px; line-height: 76px; letter-spacing: -1px; }
  .front__berry { width: 58px; height: 68px; border-radius: 50% 50% 48% 48%; background: var(--berry); opacity: .55; }
  .front__type { font-weight: 300; font-size: 54px; line-height: 62px; margin-top: 6px; }

  .claims { position: absolute; right: 0; top: 46px; width: 120px; height: 660px; }
  .claims__tab {
    position: absolute; right: 0; top: 0; width: 120px; height: 92px;
    background: var(--green-bright); border-bottom-left-radius: 40px;
    display: flex; align-items: center; justify-content: center;
    font-family: "Roboto Condensed", Arial, sans-serif; font-weight: 500; font-size: 26px;
  }
  .claims__list { position: absolute; top: 140px; width: 100%; list-style: none; }
  .claims__item {
    display: flex; flex-direction: column; align-items: center; margin-bottom: 34px;
    font-family: "Roboto Condensed", Arial, sans-serif; font-weight: 500; font-size: 25px; line-height: 1.1; text-align: center; text-transform: uppercase;
  }
  .claims__item svg { width: 44px; height: 44px; margin-bottom: 6px; }
</style>
</head>
<body>
  <section class="label" aria-label="Meadow Crunch Chews front label">
    <div class="label__top-band"></div>
    <div class="label__panel">
      <div class="label__decor" role="img" aria-label="Faint raspberry decoration"></div>
    </div>

    <div class="front">
      <p class="front__brand">RT HALVORSEN'S</p>
      <h1 class="front__title">MEADOW CRUNCH</h1>
      <p class="front__title-sub">CHEWS™</p>
      <p class="front__blend">SUPER GREENS BLEND FOR</p>
      <div class="front__rule"></div>
      <p class="front__benefits">ENERGY, DIGESTION,<small>AND IMMUNE SUPPORT*</small></p>
      <p class="front__count">60 GUMMIES <span class="front__berry" role="img" aria-label="Raspberry illustration"></span></p>
      <p class="front__type">DIETARY SUPPLEMENT</p>
    </div>

    <aside class="claims">
      <div class="claims__tab">Non-GMO</div>
      <ul class="claims__list">
        <li class="claims__item">
          <svg viewBox="0 0 44 44" fill="none" stroke="#f2f5f1" stroke-width="2.5" stroke-linejoin="round"><path d="M30 10 L12 34 L34 16 Z"/><path d="M30 10 l6-6 M32 12 l6-2"/></svg>
          Vegan<br>Friendly
        </li>
        <li class="claims__item">
          <svg viewBox="0 0 44 44" fill="none" stroke="#f2f5f1" stroke-width="2.5"><path d="M22 4 C8 16 8 32 22 40 C36 32 36 16 22 4 Z"/><path d="M22 12 V40"/></svg>
          Plant<br>Based
        </li>
        <li class="claims__item">
          <svg viewBox="0 0 44 44" fill="none" stroke="#f2f5f1" stroke-width="2.5"><rect x="14" y="8" width="16" height="28" rx="6"/><circle cx="14" cy="10" r="5"/><circle cx="30" cy="10" r="5"/><circle cx="14" cy="34" r="5"/><circle cx="30" cy="34" r="5"/></svg>
          Gelatin<br>Free
        </li>
      </ul>
    </aside>

    <div class="label__bottom-band">RASPBERRY FLAVOR GUMMIES</div>
  </section>
</body>
</html>
```